6 page (for now) squarespace website design for a Mobile Fitness small business

My sons California based small business "BrenVale Coaching" with new subsidiary called "BrenVale 4 Kids". I don't understand coding the website, is that the function squarespace provides?
In the end I want a working website, squarespace, I have a google workspace domain, email and subscription to squarespace & google workspace. URLs include brenvalecoaching.example and brenvale4kids.example. I have an idea of what I am looking for in a website and I have some examples of website designs I like, but I am 100% open to your design concepts and artistic flair. email is torin@brenvalecoaching.example
I am looking for someone to design the site, help me understand how to make "minor" changes and hopefully have a long term relationship on the tech side of the business. I need an Idea of pricing for future changes (Rate T&M).
There are 2 businesses so I need a way to incorporate both the main company and a subsidiary into 1 website or link it somehow. I am open to your suggestions how to accomplish that. Do I need 2 completely separate websites or can it be done on 1 site directing you to different pages. I read conflicting info if it is a BAD idea to link 2 different websites so I will defer to your advice.
Below are the pages I need designed:
- Home Page- BrenVale Coaching
- Home Page- BrenVale 4 Kids (Homeschool market)
- Member Page (subscription service?)
- Workouts- with video clips 1-6 min each
- About
- Contact
- FAQ's
Future work & page designs:
- Store with training subscriptions & a few merch items
- Booking Appointments
- Bookshelf
- email campaign
-Blog
I like the feel of this website:
https://zestlope.example/

```html
<!DOCTYPE html>
<html lang="en">
<head>
<meta charset="utf-8">
<title>BrenVale Coaching</title>
<link href="https://fonts.googleapis.com/css2?family=Open+Sans:wght@400;600;700;800&display=swap" rel="stylesheet">
<style>
:root{
  --ink:#1f1f1f;
  --white:#ffffff;
  --black:#000000;
  --muted:#6b6b6b;
  --line:#e4e4e4;
  --night:#10161c;
  --label:#0f0f0f;
}
*{margin:0;padding:0;box-sizing:border-box}
html,body{width:1200px;height:2996px;overflow:hidden}
body{font-family:"Open Sans",Arial,sans-serif;color:var(--ink);background:var(--white);position:relative}

/* hero */
.hero{position:absolute;top:0;left:0;width:1200px;height:680px;overflow:hidden}
.hero-photo{position:absolute;inset:0;background:
  radial-gradient(ellipse 260px 340px at 1080px 180px,rgba(245,243,238,.95),rgba(245,243,238,0) 70%),
  radial-gradient(ellipse 300px 200px at 300px 80px,rgba(200,188,172,.6),rgba(200,188,172,0) 70%),
  radial-gradient(ellipse 260px 320px at 540px 420px,rgba(30,28,28,.75),rgba(30,28,28,0) 70%),
  radial-gradient(ellipse 220px 300px at 960px 430px,rgba(40,38,38,.7),rgba(40,38,38,0) 70%),
  radial-gradient(ellipse 200px 260px at 180px 420px,rgba(35,33,33,.65),rgba(35,33,33,0) 70%),
  radial-gradient(ellipse 160px 90px at 80px 360px,rgba(190,110,70,.55),rgba(190,110,70,0) 70%),
  linear-gradient(180deg,#a79d92 0%,#8c8379 40%,#6f6a66 75%,#aaa6a2 100%)}
.hero-shade{position:absolute;inset:0;background:linear-gradient(180deg,rgba(0,0,0,.25) 0%,rgba(0,0,0,0) 30%,rgba(0,0,0,.15) 60%,rgba(0,0,0,.35) 100%)}
.site-nav{position:absolute;top:0;left:0;right:0;height:130px}
.brand{position:absolute;display:flex;flex-direction:column;align-items:center;color:var(--white);font-weight:600;letter-spacing:4px}
.site-nav .brand{left:128px;top:20px;width:172px;font-size:22px;gap:8px}
.brand-dot{display:block;border-radius:50%;border:2px solid var(--white)}
.site-nav .brand-dot{width:56px;height:56px}
.menu{position:absolute;left:430px;top:42px;display:flex;gap:34px;list-style:none}
.menu a{color:var(--white);text-decoration:none;font-size:12px;font-weight:700;letter-spacing:.5px;padding-bottom:4px}
.menu a.current{border-bottom:2px solid var(--white)}
.socials{position:absolute;display:flex;gap:12px}
.site-nav .socials{left:968px;top:38px}
.social{width:30px;height:30px;border-radius:50%;border:2px solid var(--white)}
.hero-title{position:absolute;top:456px;left:0;right:0;text-align:center;color:var(--white);font-size:46px;font-weight:700;letter-spacing:1px}
.hero-actions{position:absolute;top:540px;left:0;right:0;display:flex;justify-content:center;gap:20px}
.btn-outline{display:block;width:200px;height:38px;line-height:34px;text-align:center;border:2px solid var(--white);color:var(--white);font-size:11px;font-weight:700;letter-spacing:.5px;text-decoration:none}

/* store */
.section-title{position:absolute;left:0;width:1200px;text-align:center;font-size:36px;font-weight:800;letter-spacing:.5px;color:var(--ink)}
.store-title{top:772px}
.offer{position:absolute;width:476px;height:352px;color:var(--white);overflow:hidden}
.offer::after{content:"";position:absolute;inset:0;background:linear-gradient(180deg,rgba(0,0,0,0) 55%,rgba(0,0,0,.45) 100%)}
.offer-label{position:absolute;z-index:1;top:0;left:0;background:var(--label);height:56px;line-height:56px;padding:0 30px 0 28px;font-size:20px;font-weight:700}
.offer-caption{position:absolute;z-index:1;left:40px;bottom:34px;font-size:21px;font-weight:700}
.offer-personal{left:112px;top:856px;background:
  radial-gradient(ellipse 200px 170px at 370px 90px,rgba(240,238,232,.95),rgba(240,238,232,0) 70%),
  radial-gradient(ellipse 130px 170px at 200px 230px,rgba(40,36,34,.7),rgba(40,36,34,0) 70%),
  radial-gradient(ellipse 110px 140px at 320px 240px,rgba(60,54,50,.6),rgba(60,54,50,0) 70%),
  linear-gradient(180deg,#9d9488 0%,#7f766c 55%,#5a524b 100%)}
.offer-online{left:612px;top:856px;background:
  radial-gradient(ellipse 120px 140px at 250px 110px,rgba(214,140,90,.85),rgba(214,140,90,0) 70%),
  radial-gradient(ellipse 190px 110px at 310px 300px,rgba(70,68,68,.7),rgba(70,68,68,0) 70%),
  radial-gradient(ellipse 120px 200px at 60px 150px,rgba(92,86,80,.7),rgba(92,86,80,0) 70%),
  linear-gradient(180deg,#a59c95 0%,#8d847d 60%,#6b6560 100%)}
.offer-nutrition{left:112px;top:1240px;background:
  radial-gradient(ellipse 130px 180px at 340px 190px,rgba(120,90,150,.9),rgba(120,90,150,0) 70%),
  radial-gradient(ellipse 160px 120px at 110px 200px,rgba(230,214,70,.9),rgba(230,214,70,0) 70%),
  radial-gradient(ellipse 150px 90px at 90px 80px,rgba(226,80,90,.7),rgba(226,80,90,0) 70%),
  radial-gradient(ellipse 120px 100px at 200px 300px,rgba(110,170,90,.8),rgba(110,170,90,0) 70%),
  linear-gradient(160deg,#e7d45b 0%,#b8c864 40%,#c9a0aa 75%,#8e7890 100%)}
.offer-business{left:612px;top:1240px;background:
  radial-gradient(ellipse 110px 150px at 160px 230px,rgba(60,72,68,.8),rgba(60,72,68,0) 70%),
  radial-gradient(ellipse 110px 150px at 360px 230px,rgba(70,60,58,.75),rgba(70,60,58,0) 70%),
  radial-gradient(ellipse 220px 130px at 300px 60px,rgba(245,245,242,.95),rgba(245,245,242,0) 70%),
  linear-gradient(180deg,#e0e0dc 0%,#c4c5c1 55%,#9c9d98 100%)}

/* blog */
.blog-title{top:1696px}
.post{position:absolute;top:1780px;width:308px;height:452px;border:1px solid var(--line);box-shadow:0 2px 8px rgba(0,0,0,.08);background:var(--white)}
.post-1{left:112px}.post-2{left:444px}.post-3{left:776px}
.post-media{height:266px}
.media-gym{background:
  radial-gradient(ellipse 90px 70px at 60px 150px,rgba(90,90,90,.9),rgba(90,90,90,0) 70%),
  radial-gradient(ellipse 140px 60px at 180px 230px,rgba(120,120,120,.6),rgba(120,120,120,0) 70%),
  radial-gradient(ellipse 110px 80px at 220px 40px,rgba(80,80,80,.7),rgba(80,80,80,0) 70%),
  linear-gradient(180deg,#2c2c2c 0%,#161616 60%,#3a3a3a 100%)}
.media-scale{background:
  radial-gradient(ellipse 70px 80px at 150px 110px,rgba(160,200,220,.8),rgba(160,200,220,0) 70%),
  radial-gradient(ellipse 60px 60px at 40px 120px,rgba(120,190,60,.9),rgba(120,190,60,0) 70%),
  radial-gradient(ellipse 70px 60px at 270px 50px,rgba(232,190,70,.9),rgba(232,190,70,0) 70%),
  radial-gradient(ellipse 70px 50px at 240px 230px,rgba(210,70,60,.7),rgba(210,70,60,0) 70%),
  linear-gradient(180deg,#f3f1ea 0%,#e9e7de 100%)}
.media-group{background:
  radial-gradient(ellipse 80px 110px at 100px 170px,rgba(140,100,120,.7),rgba(140,100,120,0) 70%),
  radial-gradient(ellipse 90px 110px at 220px 180px,rgba(50,50,50,.8),rgba(50,50,50,0) 70%),
  radial-gradient(ellipse 160px 70px at 150px 40px,rgba(190,190,190,.7),rgba(190,190,190,0) 70%),
  linear-gradient(180deg,#7a7a7a 0%,#5a5a5a 50%,#3a3a3a 100%)}
.post-body{padding:28px 24px 0}
.post-title{font-size:17px;font-weight:700;margin-bottom:12px}
.post-text{font-size:11px;line-height:1.55;color:var(--muted)}

/* newsletter */
.newsletter{position:absolute;top:2316px;left:0;width:1200px;height:334px;text-align:center;color:var(--white);background:
  radial-gradient(ellipse 300px 160px at 860px 200px,rgba(60,72,84,.55),rgba(60,72,84,0) 70%),
  radial-gradient(ellipse 260px 140px at 260px 120px,rgba(48,58,68,.5),rgba(48,58,68,0) 70%),
  linear-gradient(180deg,#1a2229 0%,var(--night) 100%)}
.newsletter h2{padding-top:88px;font-size:36px;font-weight:700;letter-spacing:1px}
.newsletter p{margin-top:8px;font-size:12px;color:#d0d0d0}
.signup{margin-top:22px;display:flex;justify-content:center;gap:12px}
.signup-field{width:372px;height:42px;border:1px solid #c4c4c4;color:#e0e0e0;font-size:12px;text-align:left;padding:13px 16px}
.signup-btn{width:128px;height:42px;background:var(--white);color:var(--black);font-size:11px;font-weight:700;line-height:42px}

/* footer */
.site-footer{position:absolute;top:2650px;left:0;width:1200px;height:346px;background:var(--black);color:var(--white)}
.site-footer .brand{left:162px;top:66px;width:180px;font-size:30px;gap:12px}
.site-footer .brand-dot{width:80px;height:80px}
.footer-links{position:absolute;left:592px;top:132px;display:grid;grid-template-columns:148px 120px;row-gap:28px;list-style:none}
.footer-links a{color:var(--white);text-decoration:none;font-size:12px;font-weight:700;line-height:16px}
.site-footer .socials{left:972px;top:126px}
.copyright{position:absolute;top:274px;left:0;right:0;text-align:center;font-size:12px;font-weight:600}
.to-top{position:absolute;left:1128px;top:278px;font-size:10px;color:#cfcfcf}
</style>
</head>
<body>

<header class="hero">
  <div class="hero-photo" role="img" aria-label="Group workout class with dumbbells in a bright gym"></div>
  <div class="hero-shade"></div>
  <nav class="site-nav">
    <div class="brand"><span class="brand-dot"></span>BRENVALE</div>
    <ul class="menu">
      <li><a class="current" href="#">HOME</a></li>
      <li><a href="#">MEMBERS</a></li>
      <li><a href="#">WORKOUTS</a></li>
      <li><a href="#">ABOUT</a></li>
      <li><a href="#">CONTACT</a></li>
      <li><a href="#">FAQ'S</a></li>
    </ul>
    <div class="socials"><span class="social"></span><span class="social"></span><span class="social"></span></div>
  </nav>
  <h1 class="hero-title">BRENVALE COACHING</h1>
  <div class="hero-actions">
    <a class="btn-outline" href="#">BRENVALE COACHING</a>
    <a class="btn-outline" href="#">BRENVALE 4 KIDS</a>
  </div>
</header>

<h2 class="section-title store-title">STORE WITH TRAINING SUBSCRIPTIONS</h2>
<article class="offer offer-personal" role="img" aria-label="Trainer coaching a client with suspension straps">
  <div class="offer-label">Personal Training</div>
  <div class="offer-caption">Lorem ipsum dolor sit amet, conse</div>
</article>
<article class="offer offer-online" role="img" aria-label="Coach working on a laptop at home">
  <div class="offer-label">Online Training</div>
  <div class="offer-caption">Lorem ipsum dolor sit amet, conse</div>
</article>
<article class="offer offer-nutrition" role="img" aria-label="Shopper choosing food in a grocery aisle">
  <div class="offer-label">Nutritional Guidance</div>
  <div class="offer-caption">Lorem ipsum dolor sit amet, conse</div>
</article>
<article class="offer offer-business" role="img" aria-label="Two people reviewing work at a desk">
  <div class="offer-label">Business Coaching</div>
  <div class="offer-caption">Lorem ipsum dolor sit amet, conse</div>
</article>

<h2 class="section-title blog-title">LATEST BLOG</h2>
<article class="post post-1">
  <div class="post-media media-gym" role="img" aria-label="Dumbbells on a gym floor"></div>
  <div class="post-body">
    <h3 class="post-title">NEMO ENIM IPSAM</h3>
    <p class="post-text">Lorem ipsum dolor sit amet, conse ctetur adipiscing elit sed diam nonummy nibh euismod tincidunt ut laoreet dolore magna aliquam erat volutpat. Ut wisi enim ad minim veniam.</p>
  </div>
</article>
<article class="post post-2">
  <div class="post-media media-scale" role="img" aria-label="Bathroom scale with fruit and a tape measure"></div>
  <div class="post-body">
    <h3 class="post-title">NEMO ENIM IPSAM</h3>
    <p class="post-text">Lorem ipsum dolor sit amet, conse ctetur adipiscing elit sed diam nonummy nibh euismod tincidunt ut laoreet dolore magna aliquam erat volutpat. Ut wisi enim ad minim veniam.</p>
  </div>
</article>
<article class="post post-3">
  <div class="post-media media-group" role="img" aria-label="Friends resting after a gym session"></div>
  <div class="post-body">
    <h3 class="post-title">NEMO ENIM IPSAM</h3>
    <p class="post-text">Lorem ipsum dolor sit amet, conse ctetur adipiscing elit sed diam nonummy nibh euismod tincidunt ut laoreet dolore magna aliquam erat volutpat. Ut wisi enim ad minim veniam.</p>
  </div>
</article>

<section class="newsletter" role="img" aria-label="Dark gym backdrop behind the newsletter signup">
  <h2>SIGNUP OUR NEWSLETTER</h2>
  <p>Lorem ipsum dolor sit amet, consectetur adipiscing</p>
  <div class="signup">
    <div class="signup-field">Email address</div>
    <div class="signup-btn">SUBSCRIBE</div>
  </div>
</section>

<footer class="site-footer">
  <div class="brand"><span class="brand-dot"></span>BRENVALE</div>
  <ul class="footer-links">
    <li><a href="#">SHOP</a></li>
    <li><a href="#">CONTACT</a></li>
    <li><a href="#">ABOUT</a></li>
    <li><a href="#">STOCKISTS</a></li>
  </ul>
  <div class="socials"><span class="social"></span><span class="social"></span><span class="social"></span></div>
  <p class="copyright">© Copyright 2022 Company name | All Rights Reserved</p>
  <span class="to-top">top</span>
</footer>

</body>
</html>
```